QRV Advisors needs a web site

We need a web site for www.qrvadvisors-example.com. QRV is a mergers and acquisition consulting company that focuses our buyer and seller services on logistics companies. We help put companies together, and help with legal and financial due diligence. We want the web site to express our service and show the logistics components. We want personalized images versus pictures of trucks and airplanes.

Our new logo uses Burgandy and grey colors. Image attached. We are not in to bold, big letters...classy, artistic, low key preferred. Confidentiality, experience, professional are what we want to express on the site.

All we expect for the first part of this project is a home page, and one subpage.  We are budgeting other funds for the technical aspects of the web site

Reason: All that I'm seeing so far is trucks, forklifts and planes. We are a legal mergers and acquisitions firm that focus on logistics. I like some of the images to say logistics, but really want it say legal, financial, and putting companies together. Will pay extra for the sub page if someone can impress us with a home page.

Reason: Swamped with another project at the moment...will work on this over the weekend and provide designer feedback and select final design by Tuesday

```html
<!DOCTYPE html>
<html lang="en">
<head>
<meta charset="utf-8">
<title>QRV Advisors — Home</title>
<link href="https://fonts.googleapis.com/css2?family=Open+Sans:wght@400;600&display=swap" rel="stylesheet">
<style>
:root{
  --burgundy:#a8063d;
  --burgundy-dark:#870a31;
  --burgundy-deep:#6e0727;
  --ink:#3a3a3a;
  --text:#555;
  --muted:#888;
  --rule:#dedede;
  --page:#f3f3f3;
  --charcoal:#2b2b2b;
  --white:#fff;
}
*{box-sizing:border-box;margin:0;padding:0}
html,body{width:705px;height:1200px;overflow:hidden}
body{position:relative;background:var(--page);font-family:"Open Sans",Arial,sans-serif;color:var(--text)}
.abs{position:absolute}

/* hero */
.hero{left:0;top:0;width:705px;height:366px;background:linear-gradient(90deg,#ededed 0%,#e9e9e9 42%,#d6d9dc 55%,#c9ced3 100%);border-top:3px solid var(--burgundy)}
.hero-photo{left:300px;top:3px;width:405px;height:363px;background:linear-gradient(100deg,rgba(230,232,234,0) 0%,#bfc5cb 30%,#9ea6ad 60%,#c4c9cd 100%)}
.hero-title{left:56px;top:158px;font-size:14.5px;letter-spacing:1.2px;color:var(--ink);font-weight:400}
.hero-copy{left:57px;top:181px;width:250px;font-size:8.6px;line-height:15.2px;color:#444;letter-spacing:.2px}
.btn{display:flex;align-items:center;justify-content:center;gap:7px;color:var(--white);font-size:8.8px;border-radius:2px}
.btn-primary{left:56px;top:297px;width:92px;height:24px;background:linear-gradient(var(--burgundy),var(--burgundy-dark))}
.btn-dark{left:156px;top:297px;width:92px;height:24px;background:linear-gradient(#3b3b3b,#222)}

/* header */
.brand{left:40px;top:38px;width:184px;height:80px;background:linear-gradient(#f4f4f4,#cfcfcf);clip-path:polygon(0 0,100% 0,83% 100%,0 100%);box-shadow:0 1px 3px rgba(0,0,0,.3)}
.brand-name{left:52px;top:68px;font-size:14px;color:var(--ink);letter-spacing:.5px;display:flex;align-items:center;gap:6px}
.brand-name i{display:block;width:9px;height:9px;background:var(--burgundy)}
.nav{left:224px;top:43px;width:449px;height:71px;background:linear-gradient(var(--burgundy),var(--burgundy-dark));display:flex;border-radius:0 2px 2px 0}
.nav-item{height:71px;display:flex;flex-direction:column;align-items:center;justify-content:flex-end;padding-bottom:11px;gap:6px;color:var(--white);font-size:8.8px;letter-spacing:.6px}
.nav-item svg{width:22px;height:20px;fill:var(--white)}
.nav-item.active{background:var(--burgundy-deep)}

/* services */
.section-title{font-size:12.5px;letter-spacing:1px;color:var(--ink)}
.section-title b{font-weight:400;color:var(--burgundy)}
.services-title{left:51px;top:392px}
.search{left:542px;top:392px;width:108px;height:15px;border-bottom:2px solid #ccc;font-size:7.6px;color:var(--muted);display:flex;justify-content:space-between}
.rule{height:1px;background:var(--rule)}
.tile{width:106px;height:110px;background:linear-gradient(#f7f7f7,#e4e4e4);border-bottom:3px solid #8a8a8a;box-shadow:0 1px 3px rgba(0,0,0,.18);display:flex;align-items:center;justify-content:center}
.tile-icon{width:52px;height:52px;border-radius:50%;background:var(--burgundy)}
.arrow{width:26px;height:40px;background:var(--burgundy);top:479px}
.arrow svg{width:10px;height:10px;fill:var(--white);position:absolute;top:15px}
.service-name{width:140px;text-align:center;font-size:9.2px;color:var(--burgundy);letter-spacing:.4px;line-height:11px}
.service-copy{width:140px;text-align:center;font-size:7.6px;line-height:10.4px;color:#666;letter-spacing:.2px}
.pill{width:74px;height:15px;border-radius:8px;background:var(--burgundy-dark);color:var(--white);font-size:7.6px;display:flex;align-items:center;justify-content:center;letter-spacing:.3px}

/* testimonials */
.dots{left:622px;top:724px;display:flex;gap:3px}
.dots span{width:7px;height:7px;border-radius:50%;background:#c4c4c4}
.dots span:first-child{background:var(--burgundy)}
.quote{width:250px;font-size:7.6px;line-height:12.5px;color:#666;letter-spacing:.2px}
.quote .mark{color:#b0b0b0;font-size:15px;line-height:8px;vertical-align:-4px;margin-right:3px;font-weight:600}
.quote cite{display:block;font-style:normal;color:var(--burgundy);margin-top:2px;padding-left:2px}
.divider{left:341px;top:752px;width:1px;height:108px;background:var(--rule)}
.btn-all{left:283px;top:885px;width:117px;height:20px;background:var(--burgundy-dark);color:var(--white);font-size:7.8px;letter-spacing:.5px;display:flex;align-items:center;justify-content:center;border-radius:2px}

/* newsletter */
.newsletter{left:0;top:962px;width:705px;height:50px;background:linear-gradient(#5a5a5a,#3a3a3a)}
.newsletter-label{left:98px;top:980px;font-size:11px;color:var(--white);letter-spacing:1px}
.field{background:var(--white);border-radius:2px;font-size:7.8px;color:#999;padding:4px 7px}
.btn-sub{left:543px;top:978px;width:63px;height:21px;background:var(--burgundy-dark);color:var(--white);font-size:7.6px;letter-spacing:.5px;display:flex;align-items:center;justify-content:center;border-radius:2px}

/* footer */
.footer{left:0;top:1012px;width:705px;height:160px;background:var(--charcoal)}
.footer-head{top:1041px;font-size:9px;color:#eee;letter-spacing:.8px}
.footer-links{top:1066px;list-style:none;font-size:7.8px;color:#ddd;line-height:17.3px;letter-spacing:.2px}
.btn-send{left:196px;top:1119px;width:94px;height:18px;background:var(--burgundy-dark);color:var(--white);font-size:7.8px;display:flex;align-items:center;justify-content:center;border-radius:2px}
.bottom-bar{left:0;top:1172px;width:705px;height:28px;background:var(--burgundy)}
.copyright{left:101px;top:1182px;font-size:7.6px;color:var(--white);letter-spacing:.3px}
.social{top:1178px;width:15px;height:15px;border-radius:50%;background:var(--white)}
</style>
</head>
<body>

<!-- hero -->
<div class="abs hero"></div>
<div class="abs hero-photo" role="img" aria-label="Photograph of two business advisers shaking hands in a bright office"></div>
<h1 class="abs hero-title">QRV ADVISORS</h1>
<p class="abs hero-copy">QRV Advisors, LLC assists logistics industry business owners in &nbsp;implementing corporate growth and exit strategies. &nbsp;This includes logistics merger and acquisition (M&amp;A) advisory services along with business development consulting. &nbsp;The firm's management team consists of industry executives with extensive &nbsp;experience and relationships in the logistics industry.</p>
<a class="abs btn btn-primary">Read more <svg width="7" height="7" viewBox="0 0 10 10"><path d="M1 0L10 5 1 10z" fill="#fff"/></svg></a>
<a class="abs btn btn-dark">Contact us <svg width="9" height="7" viewBox="0 0 12 9"><rect width="12" height="9" fill="#fff"/><path d="M0 0L6 5 12 0" stroke="#222" fill="none"/></svg></a>

<!-- header -->
<div class="abs brand"></div>
<div class="abs brand-name"><i></i>QRV Advisors</div>
<nav class="abs nav">
  <div class="nav-item active" style="width:56px;margin-left:2px">
    <svg viewBox="0 0 22 20"><path d="M11 1L1 10h3v9h5v-6h4v6h5v-9h3z"/></svg>HOME</div>
  <div class="nav-item" style="width:110px">
    <svg viewBox="0 0 22 20"><path d="M4 7h4a3 3 0 1 1 6 0h4v5a3 3 0 1 1 0 6H4z"/></svg>SERVICES&#9662;</div>
  <div class="nav-item" style="width:90px">
    <svg viewBox="0 0 22 20"><path d="M11 1l10 5-10 5L1 6z"/><path d="M1 10l10 5 10-5M1 14l10 5 10-5" stroke="#fff" stroke-width="1.6" fill="none"/></svg>NEWSLETTER</div>
  <div class="nav-item" style="width:100px">
    <svg viewBox="0 0 22 20"><circle cx="7" cy="6" r="4"/><circle cx="15" cy="6" r="4"/><path d="M0 19c0-5 3-8 7-8s7 3 7 8zM10 19c0-5 1-8 5-8s7 3 7 8z"/></svg>ABOUT US</div>
  <div class="nav-item" style="width:91px">
    <svg viewBox="0 0 22 20"><rect x="1" y="4" width="20" height="14"/><path d="M1 4l10 8 10-8" stroke="#b5104a" stroke-width="1.5" fill="none"/></svg>CONTACT US</div>
</nav>

<!-- services -->
<h2 class="abs section-title services-title">OUR <b>SERVICES</b></h2>
<div class="abs search">Search...<svg width="9" height="9" viewBox="0 0 10 10"><circle cx="4" cy="4" r="3" stroke="#888" fill="none" stroke-width="1.4"/><path d="M6 6l3 3" stroke="#888" stroke-width="1.6"/></svg></div>
<div class="abs rule" style="left:45px;top:418px;width:605px"></div>

<div class="abs arrow" style="left:37px;border-radius:20px 0 0 20px"><svg viewBox="0 0 10 10" style="left:8px"><path d="M9 0L1 5 9 10z"/></svg></div>
<div class="abs arrow" style="left:626px;border-radius:0 20px 20px 0"><svg viewBox="0 0 10 10" style="left:8px"><path d="M1 0L9 5 1 10z"/></svg></div>

<div class="abs tile" style="left:54px;top:446px"><div class="tile-icon" role="img" aria-label="Icon of a target with a handshake"></div></div>
<div class="abs tile" style="left:211px;top:446px"><div class="tile-icon" role="img" aria-label="Icon of a gavel and a scroll"></div></div>
<div class="abs tile" style="left:364px;top:446px"><div class="tile-icon" role="img" aria-label="Icon of a magnifier over a document"></div></div>
<div class="abs tile" style="left:520px;top:446px"><div class="tile-icon" role="img" aria-label="Icon of a globe with a handshake"></div></div>

<h3 class="abs service-name" style="left:37px;top:564px">STRATEGIC PLANNING<br>&amp; NEGOTIATION</h3>
<h3 class="abs service-name" style="left:192px;top:564px">LEGAL DOCUMENTATION</h3>
<h3 class="abs service-name" style="left:347px;top:564px">DUE DILIGENCE</h3>
<h3 class="abs service-name" style="left:503px;top:564px">BROKERING</h3>

<p class="abs service-copy" style="left:37px;top:590px">Lorem dipsum dolora sitame adipscing elit. Morabi nisll digula astren esequat art.</p>
<p class="abs service-copy" style="left:192px;top:590px">Lorem dipsum dolora sitame adipscing elit. Morabi nisll digula astren esequat art.</p>
<p class="abs service-copy" style="left:347px;top:590px">Lorem dipsum dolora sitame adipscing elit. Morabi nisll digula astren esequat art.</p>
<p class="abs service-copy" style="left:503px;top:590px">Lorem dipsum dolora sitame adipscing elit. Morabi nisll digula astren esequat art.</p>

<a class="abs pill" style="left:69px;top:630px">more details +</a>
<a class="abs pill" style="left:225px;top:630px">more details +</a>
<a class="abs pill" style="left:380px;top:630px">more details +</a>
<a class="abs pill" style="left:536px;top:630px">more details +</a>

<!-- testimonials -->
<h2 class="abs section-title" style="left:51px;top:715px">CLIENT <b>TESTIMONIALS</b></h2>
<div class="abs dots"><span></span><span></span><span></span></div>
<div class="abs rule" style="left:45px;top:738px;width:616px"></div>

<blockquote class="abs quote" style="left:61px;top:762px"><span class="mark">&ldquo;</span>Lorem ipsum dolor sit amet, ectetur adipiscing elit. Phasellus tincidunt tellus leo, sodales vestibulum urna. hendrerit vel. Maecenas hasellus tincidunt &nbsp;ut pretium tortor vestibulum urna. Tincidunt tellus leo, sodales vestibulum urna.<cite>- John Doe, Manager</cite></blockquote>
<div class="abs divider"></div>
<blockquote class="abs quote" style="left:373px;top:762px"><span class="mark">&ldquo;</span>Lorem ipsum dolor sit amet, ectetur adipiscing elit. Phasellus tincidunt tellus leo, sodales vestibulum urna. hendrerit vel. Maecenas hasellus tincidunt &nbsp;ut pretium tortor vestibulum urna. Tincidunt tellus leo, sodales vestibulum urna.<cite>- John Doe, Manager</cite></blockquote>

<a class="abs btn-all">VIEW ALL TESTIMONIALS</a>
<div class="abs rule" style="left:45px;top:923px;width:616px"></div>

<!-- newsletter -->
<div class="abs newsletter"></div>
<div class="abs newsletter-label">SUBSCRIBE TO OUR NEWSLETTER:</div>
<div class="abs field" style="left:294px;top:978px;width:241px;height:21px;padding-top:5px">Email Address</div>
<a class="abs btn-sub">SUBSCRIBE</a>

<!-- footer -->
<div class="abs footer"></div>
<h4 class="abs footer-head" style="left:94px;font-weight:400">QUICK MESSAGE</h4>
<div class="abs field" style="left:94px;top:1070px;width:96px;height:18px">Firstname</div>
<div class="abs field" style="left:94px;top:1094px;width:96px;height:18px">Email Address</div>
<div class="abs field" style="left:94px;top:1119px;width:96px;height:18px">Contact #</div>
<div class="abs field" style="left:196px;top:1070px;width:94px;height:42px">Message</div>
<a class="abs btn-send">Send Message</a>

<h4 class="abs footer-head" style="left:366px;font-weight:400">QUICKLINKS</h4>
<ul class="abs footer-links" style="left:368px">
  <li>Home</li><li>Services</li><li>Newsletter</li><li>About us</li><li>Contact</li>
</ul>

<h4 class="abs footer-head" style="left:517px;font-weight:400">ADDITIONAL INFO</h4>
<ul class="abs footer-links" style="left:519px">
  <li>Sitemap</li><li>FAQ</li><li>Privacy Policy</li><li>Terms &amp; Agreement</li>
</ul>

<div class="abs bottom-bar"></div>
<div class="abs copyright">QRV Advisors All Rights Reserved &reg; 2014</div>
<a class="abs social" style="left:546px" aria-label="Social profile"></a>
<a class="abs social" style="left:566px" aria-label="Social profile"></a>
<a class="abs social" style="left:587px" aria-label="Social profile"></a>

</body>
</html>
```